Animal Eye Clinic needs a Business card

We are a new veterinary ophthalmology practice (Ridgeline Pet Vision Care) and we need a business card designed. We only see animal eyes - we are not a regular veterinary clinic. We already have a logo. We are looking for a professional, good looking business card to hand out to our clients. We are looking for something simple but professional and contemporary. Our logo is likely the only picture/graphic that needs to be on the card.
Updates

Contact Information for Business Card

Delia Vossman, BSc, DVM, MSc, DipACVO
Veterinary Ophthalmologist

Phone: 250.418.3927
Email: ridgelinepetvisioncare@mailbox-example.net
Website: ridgelinepetvisioncare-example.net
Address: 1874 Thornbury Rd
Kelowna, BC, V1X 4M9

Colors

Designer to choose colors to be used in the design.

Requirements
Must have
• Our logo (attached)

```html
<!DOCTYPE html>
<html lang="en">
<head>
<meta charset="utf-8">
<title>Ridgeline Pet Vision Care – Business Card</title>
<link rel="stylesheet" href="https://fonts.googleapis.com/css2?family=Lato:wght@300;400;700&display=swap">
<style>
  :root {
    --stage: #1f2022;
    --teal: #1a9aa8;
    --teal-soft: #4fb6c1;
    --paper: #ffffff;
    --accent: #7a2e35;
    --ink-light: #e8f6f8;
  }
  html, body {
    margin: 0;
    padding: 0;
    width: 1200px;
    height: 900px;
    overflow: hidden;
    background: var(--stage);
    font-family: "Lato", Arial, sans-serif;
  }
  .stage {
    position: relative;
    width: 1200px;
    height: 900px;
  }
  .card {
    position: absolute;
    left: 250px;
    width: 700px;
    height: 400px;
    display: block;
    box-shadow: 0 18px 40px rgba(0,0,0,0.55);
    border-radius: 22px;
  }
  .card--front { top: 40px; }
  .card--back { top: 460px; }
  .fill-teal { fill: var(--teal); }
  .fill-paper { fill: var(--paper); }
  .brand-name { font-family: "Lato", Arial, sans-serif; font-weight: 700; }
  .brand-name--front { fill: var(--paper); font-size: 32px; }
  .brand-name--back { fill: var(--teal); font-size: 30px; }
  .website { fill: var(--paper); font-size: 15px; font-weight: 700; letter-spacing: 2px; }
  .person-name { fill: var(--accent); font-size: 17px; font-weight: 400; letter-spacing: 0.5px; }
  .credentials { fill: var(--ink-light); font-size: 13px; font-weight: 300; }
  .job-title { fill: var(--paper); font-size: 14px; font-weight: 700; }
  .contact { fill: var(--paper); font-size: 13px; font-weight: 400; }
  .contact--address { fill: var(--accent); font-weight: 700; }
  .divider { stroke: var(--paper); stroke-width: 2; }
  .icon { fill: var(--paper); }
</style>
</head>
<body>
<main class="stage">

  <!-- Front of card -->
  <svg class="card card--front" viewBox="0 0 700 400" xmlns="http://www.w3.org/2000/svg">
    <defs>
      <clipPath id="front-shape"><rect width="700" height="400" rx="22"/></clipPath>
      <pattern id="front-teeth" width="20" height="12" patternUnits="userSpaceOnUse">
        <polygon points="0,12 10,0 20,12" fill="#ffffff"/>
      </pattern>
    </defs>
    <g clip-path="url(#front-shape)">
      <rect class="fill-teal" width="700" height="400" role="img" aria-label="Soft paw print pattern over teal background"/>
      <g transform="rotate(-5 350 340)">
        <rect x="-100" y="345" width="900" height="200" class="fill-paper"/>
        <rect x="-100" y="333" width="900" height="12" fill="url(#front-teeth)"/>
        <text class="website" x="660" y="318" text-anchor="end">www.ridgelinepetvisioncare-example.net</text>
      </g>
      <circle cx="110" cy="150" r="16" fill="#ffffff"/>
      <text class="brand-name brand-name--front" x="140" y="161">Ridgeline Pet Vision Care</text>
    </g>
  </svg>

  <!-- Back of card -->
  <svg class="card card--back" viewBox="0 0 700 400" xmlns="http://www.w3.org/2000/svg">
    <defs>
      <clipPath id="back-shape"><rect width="700" height="400" rx="22"/></clipPath>
      <pattern id="back-teeth" width="20" height="12" patternUnits="userSpaceOnUse">
        <polygon points="0,12 10,0 20,12" fill="#1a9aa8"/>
      </pattern>
    </defs>
    <g clip-path="url(#back-shape)">
      <rect class="fill-paper" width="700" height="400"/>
      <g transform="rotate(-8 350 230)">
        <rect x="-100" y="230" width="900" height="320" class="fill-teal"/>
        <rect x="-100" y="218" width="900" height="12" fill="url(#back-teeth)"/>
      </g>

      <circle cx="70" cy="118" r="14" fill="#1a9aa8"/>
      <text class="brand-name brand-name--back" x="96" y="129">Ridgeline Pet Vision Care</text>

      <g class="person">
        <text class="person-name" x="312" y="300" text-anchor="end">DELIA VOSSMAN</text>
        <text class="credentials" x="312" y="322" text-anchor="end">BSc, DVM, MSc, DipACVO</text>
        <text class="job-title" x="312" y="346" text-anchor="end">Veterinary Ophthalmologist</text>
      </g>

      <line class="divider" x1="330" y1="280" x2="330" y2="365"/>

      <g class="contacts">
        <path class="icon" d="M350 286c1-1 3-1 4 0l2 2c1 1 1 2 0 3l-1 1c1 2 3 4 5 5l1-1c1-1 2-1 3 0l2 2c1 1 1 3 0 4l-1 1c-5 1-15-9-16-15z"/>
        <text class="contact" x="374" y="298">250.418.3927</text>
        <rect class="icon" x="350" y="312" width="15" height="10" rx="1"/>
        <path d="M350 312l7.5 6 7.5-6" fill="none" stroke="#1a9aa8" stroke-width="1.2"/>
        <text class="contact" x="374" y="322">ridgelinepetvisioncare@mailbox-example.net</text>
        <text class="contact contact--address" x="350" y="346">1874 Thornbury Rd, Kelowna, BC, V1X 4M9</text>
      </g>
    </g>
  </svg>

</main>
</body>
</html>
```